Restaurant Finder Website Design

I need to create a website that will help people find restaurants around a zip code or address.

I would like to have a very clean and simple design. I will need a design for the homepage, that should be very clean and simple to use. its where the users will launch their search. I am thinking something like tavuro like.. big search field with a very clean page where users can create an account or restaurants subscribe to the service.

Also need the design of the search results page, I would like to display a big map with the results and a list on the side or the bottom of the map.

Also need a profile page for the users that sign up to the site.

Mostly what I need are guidelines and color coordinated elements, like a general layout and buttons that work together. I would like to know what the action buttons and elements should look like. Because its going to have some more detail pages.

Target Market(s)

People in general, mainly people that work at an office and have to find a place for lunch every day.

Industry/Entity Type

Restaurant

Number of Pages Required

4 page

Font styles to use
Serif
Sans Serif

Requirements
Must have
• It must be a really simple and clean design but look edgy.

```html
<!DOCTYPE html>
<html lang="en">
<head>
<meta charset="utf-8">
<title>LunchLoop – Find restaurants near you</title>
<link rel="stylesheet" href="https://fonts.googleapis.com/css2?family=Rubik:wght@400;500&family=Open+Sans:wght@400&display=swap">
<style>
  :root {
    --brand-red: #c61f27;
    --ink: #26272b;
    --black: #050505;
    --white: #ffffff;
    --panel: rgba(236, 236, 236, 0.82);
    --placeholder: #6b6b6b;
    --photo-warm: #b98a63;
    --photo-light: #e9ddd0;
    --photo-dark: #3a2a22;
  }
  * { box-sizing: border-box; margin: 0; padding: 0; }
  html, body { width: 1200px; height: 655px; overflow: hidden; }
  body { font-family: "Rubik", sans-serif; color: var(--ink); }

  .page {
    position: relative;
    width: 1200px;
    height: 655px;
    overflow: hidden;
  }
  .hero-photo {
    position: absolute;
    inset: 0;
    background:
      radial-gradient(ellipse at 25% 20%, var(--photo-light) 0%, rgba(233,221,208,0) 45%),
      radial-gradient(ellipse at 80% 15%, #d9d4c8 0%, rgba(217,212,200,0) 40%),
      radial-gradient(ellipse at 10% 70%, #c98a4c 0%, rgba(201,138,76,0) 35%),
      linear-gradient(160deg, var(--photo-warm) 0%, #d8c7b3 45%, #a07552 75%, var(--photo-dark) 100%);
  }
  .panel {
    position: absolute;
    left: 59px;
    top: 80px;
    width: 1081px;
    height: 485px;
    background: var(--panel);
  }
  .brand {
    position: absolute;
    left: 455px;
    top: 128px;
    display: flex;
    align-items: center;
    gap: 16px;
  }
  .brand-mark {
    width: 56px;
    height: 56px;
    border-radius: 50%;
    background: var(--brand-red);
  }
  .brand-name {
    font-family: "Rubik", sans-serif;
    font-weight: 500;
    font-size: 38px;
    color: var(--ink);
    letter-spacing: -0.3px;
  }
  .search-card {
    position: absolute;
    left: 227px;
    top: 256px;
    width: 732px;
    height: 184px;
    background: var(--brand-red);
  }
  .search-title {
    position: absolute;
    left: 26px;
    top: 22px;
    font-size: 19.5px;
    font-weight: 400;
    color: var(--white);
  }
  .search-form {
    position: absolute;
    left: 31px;
    top: 66px;
    width: 674px;
    height: 50px;
    display: flex;
  }
  .search-icon {
    position: absolute;
    left: -15px;
    top: 9px;
    width: 32px;
    height: 32px;
  }
  .search-input {
    flex: 1;
    height: 50px;
    border: 0;
    background: var(--white);
    padding-left: 28px;
    font-family: "Open Sans", sans-serif;
    font-size: 16px;
    color: var(--ink);
    outline: none;
  }
  .search-input::placeholder { color: var(--placeholder); }
  .search-button {
    width: 123px;
    height: 50px;
    border: 0;
    background: var(--black);
    color: var(--white);
    font-family: "Rubik", sans-serif;
    font-size: 20px;
    letter-spacing: 0.5px;
    cursor: pointer;
  }
  .account-links {
    position: absolute;
    left: 0;
    right: 0;
    top: 141px;
    text-align: center;
    font-family: "Open Sans", sans-serif;
    font-size: 15px;
    color: var(--white);
  }
  .account-links a { color: var(--white); text-decoration: none; }
  .account-links .divider { color: #8e151b; margin: 0 6px; }
  .copyright {
    position: absolute;
    left: 0;
    width: 1200px;
    top: 529px;
    text-align: center;
    font-size: 12px;
    color: var(--ink);
  }
</style>
</head>
<body>
  <main class="page">
    <div class="hero-photo" role="img" aria-label="Close-up photo of a Mediterranean platter with salsa dip, olives and pita bread"></div>
    <section class="panel"></section>

    <div class="brand">
      <span class="brand-mark"></span>
      <span class="brand-name">LunchLoop</span>
    </div>

    <section class="search-card">
      <h1 class="search-title">We help people find restaurants arround a zip code or address</h1>
      <form class="search-form">
        <svg class="search-icon" viewBox="0 0 32 32" aria-hidden="true">
          <circle cx="16" cy="16" r="16" fill="#050505"/>
          <circle cx="14" cy="14" r="5.5" fill="none" stroke="#fff" stroke-width="2.4"/>
          <line x1="18" y1="18" x2="23" y2="23" stroke="#fff" stroke-width="2.8" stroke-linecap="round"/>
        </svg>
        <input class="search-input" type="text" placeholder="Enter your zip code or Address">
        <button class="search-button" type="submit">SEARCH</button>
      </form>
      <nav class="account-links">
        <a href="#">Create account</a><span class="divider">|</span><a href="#">Login your account</a>
      </nav>
    </section>

    <footer class="copyright">© 2016 Copyright Lunch Loop All Rights Reserved</footer>
  </main>
</body>
</html>
```